Real Estate Sign to Help Modernize and Make it POP!

Design a sign style that would be good for marketing the sale or lease of properties. This will be 3 ' x 4' when printed and needs to look professional, modern, and catchy. It should us the company name, logo, and phone number at a minimum. Keep with the color scheme but open to varieties.

It will be printed and put in a large wooden frame as shown in one of the pictures.

Target Market(s)

Buyers and Tenants

Industry/Entity Type

Real Estate

Requirements
Must have
• company name, logo, and phone number
same color scheme as sign and website
Nice to have
• My Name, "Mervin Kalloway, CCIM"
Company Website
Ability to have an easy change from FOR SALE to FOR LEASE or FOR SALE/LEASE when I need to move this sign to a new property
An ability to have reflective colors printed on the contrast for cars to see at night
Should not have
• "Property Managed by"

```html
<!DOCTYPE html>
<html lang="en">
<head>
<meta charset="utf-8">
<title>Harbor Point Realty – For Sale Sign</title>
<link rel="stylesheet" href="https://fonts.googleapis.com/css2?family=Montserrat:wght@600;700;800;900&display=swap">
<style>
  :root {
    --teal: #4a716c;
    --sage: #97ab84;
    --sage-light: #a7b994;
    --navy: #2f3541;
    --white: #ffffff;
    --backdrop: #4b4b4b;
  }
  html, body {
    margin: 0;
    padding: 0;
    width: 707px;
    height: 1200px;
    overflow: hidden;
    background: var(--backdrop);
  }
  .canvas {
    position: relative;
    width: 707px;
    height: 1200px;
  }
  .sale-sign {
    position: absolute;
    left: 23px;
    top: 353px;
    width: 660px;
    height: 493px;
    box-shadow: 0 12px 30px rgba(0,0,0,0.45);
    display: block;
  }
  .headline {
    font-family: "Montserrat", sans-serif;
    font-weight: 900;
    font-size: 240px;
  }
  .phone {
    font-family: "Montserrat", sans-serif;
    font-weight: 800;
    font-size: 96px;
    fill: var(--white);
  }
  .website {
    font-family: "Montserrat", sans-serif;
    font-weight: 700;
    font-size: 50px;
    fill: var(--white);
  }
  .brand-name {
    font-family: "Montserrat", sans-serif;
    font-weight: 600;
    font-size: 30px;
    letter-spacing: 3px;
    fill: var(--teal);
  }
</style>
</head>
<body>
<main class="canvas">
  <svg class="sale-sign" viewBox="0 0 1045 781" xmlns="http://www.w3.org/2000/svg" aria-label="For sale sign, Harbor Point Realty">
    <defs>
      <clipPath id="teal-side">
        <polygon points="0,0 325,0 700,560 0,560"/>
      </clipPath>
      <clipPath id="white-side">
        <polygon points="325,0 1045,0 1045,560 700,560"/>
      </clipPath>
    </defs>

    <!-- base panels -->
    <rect class="panel-white" width="1045" height="781" fill="var(--white)"/>
    <polygon class="panel-teal" points="0,0 325,0 690,535 1045,535 1045,781 0,781" fill="var(--teal)"/>
    <polygon class="accent-sage-top" points="712,505 1045,505 1045,540 690,540" fill="var(--sage)"/>
    <polygon class="accent-sage-left" points="0,520 185,781 0,781" fill="var(--sage)"/>
    <polygon class="accent-sage-bottom" points="625,668 1045,668 1045,781 555,781" fill="var(--sage)"/>
    <polygon class="accent-sage-corner" points="760,668 1045,668 1045,781 850,781" fill="var(--sage-light)"/>
    <polygon class="band-phone" points="70,535 1045,535 1045,668 160,668" fill="var(--navy)"/>

    <!-- headline on teal side -->
    <g class="headline-teal" clip-path="url(#teal-side)">
      <text class="headline" x="92" y="272" textLength="485" lengthAdjust="spacingAndGlyphs" fill="none" stroke="var(--white)" stroke-width="3">FOR</text>
      <text class="headline" x="80" y="262" textLength="480" lengthAdjust="spacingAndGlyphs" fill="var(--white)">FOR</text>
      <text class="headline" x="92" y="490" textLength="595" lengthAdjust="spacingAndGlyphs" fill="none" stroke="var(--white)" stroke-width="3">SALE</text>
      <text class="headline" x="80" y="480" textLength="590" lengthAdjust="spacingAndGlyphs" fill="var(--white)">SALE</text>
    </g>
    <!-- headline on white side -->
    <g class="headline-white" clip-path="url(#white-side)">
      <text class="headline" x="92" y="272" textLength="485" lengthAdjust="spacingAndGlyphs" fill="none" stroke="var(--teal)" stroke-width="3">FOR</text>
      <text class="headline" x="80" y="262" textLength="480" lengthAdjust="spacingAndGlyphs" fill="var(--teal)">FOR</text>
      <text class="headline" x="92" y="490" textLength="595" lengthAdjust="spacingAndGlyphs" fill="none" stroke="var(--teal)" stroke-width="3">SALE</text>
      <text class="headline" x="80" y="480" textLength="590" lengthAdjust="spacingAndGlyphs" fill="var(--teal)">SALE</text>
    </g>

    <!-- brand -->
    <g class="brand">
      <circle cx="818" cy="120" r="58" fill="var(--teal)"/>
      <text class="brand-name" x="818" y="258" text-anchor="middle" textLength="330" lengthAdjust="spacingAndGlyphs">HARBOR POINT REALTY</text>
    </g>

    <!-- contact -->
    <text class="phone" x="195" y="637" textLength="790" lengthAdjust="spacingAndGlyphs">555-210-7746</text>
    <text class="website" x="195" y="748" textLength="790" lengthAdjust="spacingAndGlyphs">HarborPointRealty.com</text>
  </svg>
</main>
</body>
</html>
```